Business Card Design Project

Keep it simple , using logo and colors that compliment. Logo on one side with complimentary back ground color. Other side, personal info with possible complimentary design/colors

Target Market(s)

we are a non for profit that will be seeking donations . Both monetary and in kind

Industry/Entity Type

Business

Font styles to use
Sans Serif

Colors

Designer to choose colors to be used in the design.

```html
<!DOCTYPE html>
<html lang="en">
<head>
<meta charset="utf-8">
<title>Rise Together – Business Card</title>
<link rel="stylesheet" href="https://fonts.googleapis.com/css2?family=Lato:wght@400;700;900&display=swap">
<style>
  :root {
    --navy: #1f2550;
    --navy-deep: #181d42;
    --yellow: #e6d411;
    --paper: #fbfbfb;
    --ink: #1b1f3a;
    --backdrop: #363636;
  }
  * { margin: 0; padding: 0; box-sizing: border-box; }
  html, body {
    width: 1200px; height: 997px; overflow: hidden;
    background: var(--backdrop);
    font-family: "Lato", sans-serif;
  }
  .card {
    position: absolute; left: 320px;
    width: 560px; height: 320px;
    border-radius: 22px; overflow: hidden;
    box-shadow: 0 16px 40px rgba(0,0,0,.45);
  }
  /* Logo side */
  .card--brand { top: 110px; background: var(--navy); }
  .card--brand .brand {
    position: absolute; inset: 0;
    display: flex; align-items: center; justify-content: center; gap: 16px;
  }
  .brand__dot {
    width: 22px; height: 22px; border-radius: 50%;
    background: var(--yellow);
  }
  .brand__name {
    font-weight: 400; font-size: 44px; color: var(--yellow);
    letter-spacing: .5px;
  }
  /* Info side */
  .card--info { top: 530px; background: var(--paper); }
  .card__bands { position: absolute; inset: 0; }
  .card--info .brand {
    position: absolute; left: 34px; top: 0; bottom: 0;
    display: flex; align-items: center; gap: 12px;
  }
  .card--info .brand__dot { width: 18px; height: 18px; background: var(--navy); }
  .card--info .brand__name { font-size: 26px; color: var(--navy); }
  .divider {
    position: absolute; left: 262px; top: 82px;
    width: 5px; height: 166px; background: var(--navy);
  }
  .person { position: absolute; left: 290px; top: 78px; }
  .person__name {
    font-weight: 900; font-size: 20px; color: var(--ink); letter-spacing: .3px;
  }
  .person__role {
    font-weight: 900; font-size: 13px; color: var(--yellow);
    letter-spacing: .4px; margin-top: 2px;
  }
  .contacts { list-style: none; position: absolute; left: 290px; top: 156px; }
  .contacts li {
    display: flex; align-items: center; gap: 9px;
    font-weight: 700; font-size: 14px; color: var(--ink);
    height: 23px;
  }
  .contacts svg { width: 18px; height: 18px; flex: none; }
</style>
</head>
<body>

<section class="card card--brand">
  <div class="brand">
    <span class="brand__dot"></span>
    <span class="brand__name">Rise Together</span>
  </div>
</section>

<section class="card card--info">
  <svg class="card__bands" viewBox="0 0 560 320" width="560" height="320">
    <path d="M30 0 H560 V18 H78 C56 18 48 0 30 0 Z" fill="var(--navy-deep)"/>
    <path d="M26 -1 C46 -1 52 22 78 22 H560" fill="none" stroke="var(--yellow)" stroke-width="3"/>
    <path d="M0 320 V302 H482 C504 302 512 320 530 320 Z" fill="var(--navy-deep)"/>
    <path d="M0 298 H482 C508 298 514 321 534 321" fill="none" stroke="var(--yellow)" stroke-width="3"/>
  </svg>

  <div class="brand">
    <span class="brand__dot"></span>
    <span class="brand__name">Rise Together</span>
  </div>

  <div class="divider"></div>

  <div class="person">
    <div class="person__name">YOUR NAME</div>
    <div class="person__role">OWNER &amp; DIRECTOR</div>
  </div>

  <ul class="contacts">
    <li>
      <svg viewBox="0 0 18 18"><rect width="18" height="18" rx="4" fill="var(--navy)"/>
        <path d="M4 6 C4 4 14 4 14 6 L12 7.5 L11 6.5 H7 L6 7.5 Z M5 13 L6 8.5 H12 L13 13 Z" fill="#fff"/></svg>
      0044 20 7946 0321
    </li>
    <li>
      <svg viewBox="0 0 18 18"><rect width="18" height="18" rx="4" fill="var(--navy)"/>
        <rect x="6" y="3.5" width="6" height="3.5" fill="#fff"/><rect x="3.5" y="7" width="11" height="5" rx="1" fill="#fff"/><rect x="6" y="11" width="6" height="3.5" fill="#fff" stroke="var(--navy)" stroke-width=".8"/></svg>
      0044 20 7946 0311
    </li>
    <li>
      <svg viewBox="0 0 18 18"><rect width="18" height="18" rx="4" fill="var(--navy)"/>
        <rect x="3.5" y="5" width="11" height="8" fill="none" stroke="#fff" stroke-width="1.4"/><path d="M3.5 5 L9 10 L14.5 5" fill="none" stroke="#fff" stroke-width="1.4"/></svg>
      hello@risetogether.org
    </li>
    <li>
      <svg viewBox="0 0 18 18"><rect width="18" height="18" rx="4" fill="var(--navy)"/>
        <path d="M8 10 L10 8 M7.5 7.5 L5.5 9.5 A2 2 0 0 0 8.5 12.5 L10 11 M10.5 10.5 L12.5 8.5 A2 2 0 0 0 9.5 5.5 L8 7" fill="none" stroke="#fff" stroke-width="1.5" stroke-linecap="round"/></svg>
      www.risetogether.org
    </li>
  </ul>
</section>

</body>
</html>
```